Heavy Duty Repairs Poster

Good afternoon - I'm looking for a poster , design to set up around different areas. The Poster must consist of the following
- Heavy duty repairs
- Pictures of Semi trucks , heavy construction equipment , trailers
- Agriculture
- All north American equipment ( see attached pictures)
- Brief Descriptions in bullet point forms
CVIPS
WELDING
AIR CONDITIONING
ENGINE REBUILDS
DIAGONSTICS
FLEET MANAGMENT
TIRE REPAIR AND SALES
ELECTRICAL , HYDRALIC , POWER TRAIN SERVICE AND REPAIRS
PART SALES
FLEET MAINTINACE
DELTEING AND TUNING
AFTER MARKET INSTALLS OUTFITTING
ONSITE & OFFSITE REPAIRS
FULL RECERTIFACTION OVERHAULING
Warranty Approved

Target Market(s)

Heavy Duty Truck , Equipment , Agriculture Owners

Industry/Entity Type

Heavy Duty Repairs

Colors
EB3D1F
EC4F4E
F09395
F8D3D4
FCEDEE

Requirements
Must have
• Pictures of : Semi trucks and trailer , Construction heavy equipment , agriculture equipment
Nice to have
• Flashy and stands out

```html
<!DOCTYPE html>
<html lang="en">
<head>
<meta charset="utf-8">
<title>Heavy Duty Repairs Poster</title>
<link href="https://fonts.googleapis.com/css2?family=Exo+2:wght@600;800&family=Montserrat:wght@400;600&display=swap" rel="stylesheet">
<style>
  :root {
    --page: #ffffff;
    --ink: #111111;
    --red: #eb3d1f;
    --coral: #ec4f4e;
    --pink: #f09395;
    --blush: #f8d3d4;
    --black: #000000;
    --white: #ffffff;
  }
  html, body {
    margin: 0;
    width: 1200px;
    height: 1200px;
    overflow: hidden;
    background: var(--page);
  }
  .poster {
    position: absolute;
    left: 241px;
    top: 60px;
    width: 725px;
    height: 1087px;
    outline: 1px solid var(--ink);
  }
  .poster svg { display: block; }
  .headline {
    font-family: "Exo 2", sans-serif;
    font-weight: 600;
    fill: var(--red);
  }
  .service {
    font-family: "Montserrat", sans-serif;
    font-weight: 400;
    font-size: 17px;
    fill: var(--white);
  }
  .tick {
    fill: none;
    stroke: var(--white);
    stroke-width: 2.6;
    stroke-linecap: round;
    stroke-linejoin: round;
  }
  .company {
    font-family: "Montserrat", sans-serif;
    font-weight: 600;
    fill: var(--white);
  }
  .phone {
    font-family: "Exo 2", sans-serif;
    font-weight: 800;
    fill: var(--red);
  }
</style>
</head>
<body>
<div class="poster">
  <svg width="725" height="1087" viewBox="0 0 725 1087" xmlns="http://www.w3.org/2000/svg">
    <defs>
      <linearGradient id="photoTone" x1="0" y1="0" x2="1" y2="1">
        <stop offset="0" stop-color="#c9603a"/>
        <stop offset="0.45" stop-color="#8a7565"/>
        <stop offset="1" stop-color="#6e5a48"/>
      </linearGradient>
    </defs>

    <rect class="sheet" width="725" height="1087" fill="var(--white)"/>

    <polygon class="hero-photo" role="img"
      aria-label="Photo of an orange excavator with its bucket in the foreground, digging on a dirt work site"
      points="0,62 395,62 395,330 725,330 725,372 0,532"
      fill="url(#photoTone)"/>

    <text class="headline" x="683" y="139" font-size="100" text-anchor="end">Heavy</text>
    <text class="headline" x="650" y="224" font-size="100" text-anchor="end">Duty</text>
    <text class="headline" x="683" y="302" font-size="84" text-anchor="end">Repairs</text>

    <polygon class="accent-band" points="0,527 725,370 725,1087 0,1087" fill="var(--coral)"/>
    <polygon class="service-panel" points="0,541 725,429 725,864 0,864" fill="var(--red)"/>
    <rect class="footer" x="0" y="864" width="725" height="223" fill="var(--black)"/>

    <g class="warranty-seal">
      <circle cx="597" cy="484" r="75" fill="var(--black)" stroke="var(--white)" stroke-width="1.5"/>
      <circle cx="597" cy="484" r="44" fill="none" stroke="var(--white)" stroke-width="1.2"/>
    </g>

    <g class="services-left">
      <g transform="translate(81,570)"><polyline class="tick" points="0,2 5,8 14,-6"/></g>
      <text class="service" x="105" y="576">CVIPS</text>
      <g transform="translate(81,600)"><polyline class="tick" points="0,2 5,8 14,-6"/></g>
      <text class="service" x="105" y="606">WELDING</text>
      <g transform="translate(81,630)"><polyline class="tick" points="0,2 5,8 14,-6"/></g>
      <text class="service" x="105" y="636">AIR CONDITIONING</text>
      <g transform="translate(81,660)"><polyline class="tick" points="0,2 5,8 14,-6"/></g>
      <text class="service" x="105" y="666">ENGINE REBUILDS</text>
      <g transform="translate(81,690)"><polyline class="tick" points="0,2 5,8 14,-6"/></g>
      <text class="service" x="105" y="696">DIAGONSTICS</text>
      <g transform="translate(81,720)"><polyline class="tick" points="0,2 5,8 14,-6"/></g>
      <text class="service" x="105" y="726">FLEET MANAGMENT</text>
      <g transform="translate(81,750)"><polyline class="tick" points="0,2 5,8 14,-6"/></g>
      <text class="service" x="105" y="756">TIRE REPAIR AND SALES</text>
      <g transform="translate(81,780)"><polyline class="tick" points="0,2 5,8 14,-6"/></g>
      <text class="service" x="105" y="786">ELECTRICAL , HYDRALIC ,</text>
      <text class="service" x="105" y="807">POWER TRAIN SERVICE AND</text>
      <text class="service" x="105" y="828">REPAIRS</text>
    </g>

    <g class="services-right">
      <g transform="translate(409,570)"><polyline class="tick" points="0,2 5,8 14,-6"/></g>
      <text class="service" x="432" y="576">PART SALES</text>
      <g transform="translate(409,600)"><polyline class="tick" points="0,2 5,8 14,-6"/></g>
      <text class="service" x="432" y="606">FLEET MAINTINACE</text>
      <g transform="translate(409,630)"><polyline class="tick" points="0,2 5,8 14,-6"/></g>
      <text class="service" x="432" y="636">DELTEING AND TUNING</text>
      <g transform="translate(409,660)"><polyline class="tick" points="0,2 5,8 14,-6"/></g>
      <text class="service" x="432" y="666">AFTER MARKET INSTALLS</text>
      <g transform="translate(409,690)"><polyline class="tick" points="0,2 5,8 14,-6"/></g>
      <text class="service" x="432" y="696">OUTFITTING</text>
      <g transform="translate(409,720)"><polyline class="tick" points="0,2 5,8 14,-6"/></g>
      <text class="service" x="432" y="726">ONSITE &amp; OFFSITE REPAIRS</text>
      <g transform="translate(409,750)"><polyline class="tick" points="0,2 5,8 14,-6"/></g>
      <text class="service" x="432" y="756">FULL RECERTIFACTION</text>
      <g transform="translate(409,780)"><polyline class="tick" points="0,2 5,8 14,-6"/></g>
      <text class="service" x="432" y="786">OVERHAULING</text>
    </g>

    <text class="company" x="362" y="950" font-size="25" text-anchor="middle">Ridgeline Mechanical Services</text>
    <text class="company" x="362" y="984" font-size="19" text-anchor="middle">Birchwood , Alberta</text>
    <text class="phone" x="362" y="1043" font-size="54" text-anchor="middle">780-555-0147</text>
  </svg>
</div>
</body>
</html>
```